A4 Single Sided Brochure Folder Design Technical Company

We are a technical company based in the UK, working worldwide for Power Distribution companies.

We have technical literature and need a folder to present these in. The design should be very simple and clean using our logo and "Innovative Utility Solutions"

Our website kestrome.com gives and idea of the business but don't follow the look of the website as we will be redoing shortly.

• Logo and Strap Line
• Clean, easy to print and timeless
• Shouldn't be fashionable, we certainly aren't

```html
<!DOCTYPE html>
<html lang="en">
<head>
<meta charset="utf-8">
<title>Kestrome Presentation Folder</title>
<link href="https://fonts.googleapis.com/css2?family=Lato:wght@300;400&family=Quicksand:wght@500&display=swap" rel="stylesheet">
<style>
  :root {
    --backdrop: #e9e6e2;
    --paper: #ffffff;
    --brand-magenta: #b5318f;
    --tagline-grey: #8a8a8a;
    --url-grey: #444444;
    --fold-line: #c9b3a6;
  }
  html, body {
    margin: 0;
    padding: 0;
    width: 1200px;
    height: 1200px;
    overflow: hidden;
    background: var(--backdrop);
  }
  .folder-spread {
    position: relative;
    width: 1200px;
    height: 1200px;
  }
  .folder-cover {
    position: absolute;
    left: 102px;
    top: 131px;
    width: 1030px;
    height: 719px;
    background: var(--paper);
  }
  .cover-rule {
    position: absolute;
    left: 0;
    top: 706px;
    width: 100%;
    height: 6px;
    background: var(--brand-magenta);
  }
  .brand-block {
    position: absolute;
    left: 610px;
    top: 400px;
    width: 330px;
    text-align: center;
  }
  .brand-name {
    margin: 0;
    font-family: "Quicksand", sans-serif;
    font-weight: 500;
    font-size: 66px;
    line-height: 1;
    letter-spacing: 1px;
    color: var(--brand-magenta);
  }
  .brand-tagline {
    margin: 22px 0 0;
    font-family: "Lato", sans-serif;
    font-weight: 300;
    font-size: 25px;
    color: var(--tagline-grey);
    white-space: nowrap;
  }
  .cover-url {
    position: absolute;
    left: 210px;
    top: 652px;
    margin: 0;
    font-family: "Lato", sans-serif;
    font-weight: 400;
    font-size: 13px;
    color: var(--url-grey);
  }
  .pocket-flap {
    position: absolute;
    left: 0;
    top: 0;
  }
</style>
</head>
<body>
  <div class="folder-spread">
    <div class="folder-cover">
      <div class="brand-block">
        <h1 class="brand-name">Kestrome</h1>
        <p class="brand-tagline">Innovative Utility Solutions</p>
      </div>
      <p class="cover-url">www.kestrome.com</p>
      <div class="cover-rule"></div>
    </div>
    <svg class="pocket-flap" width="1200" height="1200" viewBox="0 0 1200 1200" aria-hidden="true">
      <polygon points="64,860 102,850 616,850 544,1064 102,1064 64,1058" fill="#ffffff"/>
      <line x1="102" y1="850" x2="102" y2="1064" stroke="var(--fold-line)" stroke-width="0.8"/>
      <line x1="102" y1="850.5" x2="616" y2="850.5" stroke="var(--fold-line)" stroke-width="0.6"/>
    </svg>
  </div>
</body>
</html>
```